Corvana Tongue Works, LLC

We need a business card that includes information about our business and conveys a reliable business that provides document translation services and interpreters for a variety of corporate and individual clients. We want to come across as professional, reliable, yet approachable. It should include the following on one side:

ESL / ENL Language Classes, Private Lessons, and Online Tutors
PLEXA Training and Testing
Translating & Interpreting Services
Contact us about Over-the-Phone Interpreting in over 200 languages
24/7/365
www.corvanatongue.example

The other side should include (555) 481-3062

Rhoda Pelling, President
482 Garnet Ave., Ste. 219
Indianapolis, IN 40917

Please add USA as part of the address. Also, please add rmpelling@corvanatongueworks.example as the e-mail address. Thank you.

Target Market(s)

Business professionals, their families, the international community

Industry/Entity Type

Business

Contact Information for Business Card

24/7/365
www.corvanatongue.example

(555) 481-3062

Rhoda Pelling, President
482 Garnet Ave., Ste. 219
Indianapolis, IN 40917
USA

Font styles to use
Sans Serif

Colors

Designer to choose colors to be used in the design.

Requirements
Must have
• See project description
• e-mail address and web address
• Phone number
Nice to have
• a globe
• physical address
Should not have
• Should not have the same color scheme as other agencies in our market in Indiana unless it is blue and black. No purple or yellow.

```html
<!DOCTYPE html>
<html lang="en">
<head>
<meta charset="utf-8">
<title>Corvana Tongue Works, LLC — Business Card</title>
<link href="https://fonts.googleapis.com/css2?family=Open+Sans:wght@400;600;700&display=swap" rel="stylesheet">
<style>
  :root {
    --backdrop: #e4e4e4;
    --card-dark: #2f3133;
    --card-dark-map: #3a3d40;
    --brand-blue: #1e96d2;
    --ink: #2a2a2a;
    --ink-soft: #555;
    --paper: #ffffff;
    --on-dark: #e9ecef;
  }
  * { box-sizing: border-box; margin: 0; padding: 0; }
  html, body { width: 1200px; height: 852px; overflow: hidden; }
  body {
    background: var(--backdrop);
    font-family: "Open Sans", Arial, sans-serif;
    position: relative;
  }
  .card {
    position: absolute;
    width: 540px;
    height: 309px;
    border-radius: 18px;
    overflow: hidden;
    box-shadow: 0 6px 18px rgba(0,0,0,0.18);
  }

  /* Services side */
  .card--services {
    left: 40px; top: 150px;
    background: var(--card-dark);
    color: var(--on-dark);
  }
  .world-map-area {
    position: absolute;
    left: 40px; top: 30px;
    width: 460px; height: 230px;
    border-radius: 40%;
    background: radial-gradient(ellipse at center, var(--card-dark-map) 0%, var(--card-dark) 72%);
  }
  .services {
    position: absolute;
    left: 0; right: 0; top: 44px;
    text-align: center;
    font-size: 15px;
    line-height: 1.45;
  }
  .services .bullet { color: var(--brand-blue); margin-right: 5px; }
  .services .sep { margin-left: 12px; }
  .services__rule {
    width: 250px; height: 1px;
    margin: 10px auto 8px;
    background: var(--brand-blue);
  }
  .services__contact { font-size: 14.5px; line-height: 1.4; }
  .web {
    position: absolute;
    left: 0; right: 0; bottom: 26px;
    text-align: center;
    font-size: 14px;
  }
  .web .accent { color: var(--brand-blue); }

  /* Contact side */
  .card--contact {
    left: 620px; top: 392px;
    background: var(--paper);
  }
  .card__waves { position: absolute; inset: 0; }
  .brand {
    position: absolute;
    left: 240px; top: 24px;
    display: flex; align-items: center; gap: 12px;
  }
  .brand__dot {
    width: 64px; height: 64px; border-radius: 50%;
    background: var(--brand-blue);
    flex: none;
  }
  .brand__name {
    font-size: 21px; font-weight: 600; line-height: 1.1;
    color: var(--ink);
  }
  .person {
    position: absolute;
    left: 30px; top: 118px;
  }
  .person__name { font-size: 19px; font-weight: 700; color: var(--brand-blue); line-height: 1.3; }
  .person__title { font-size: 11.5px; color: var(--ink-soft); margin-top: 1px; }
  .edge-dot {
    position: absolute;
    left: -14px; top: 126px;
    width: 28px; height: 28px; border-radius: 50%;
    background: var(--brand-blue);
  }
  .tagline {
    position: absolute;
    right: 26px; top: 190px;
    text-align: right;
    font-size: 12.5px; line-height: 1.45;
    color: var(--paper);
  }
  .contact {
    position: absolute;
    left: 30px; top: 214px;
    color: var(--paper);
    font-size: 12px; line-height: 1.35;
    list-style: none;
  }
  .contact li { display: flex; align-items: center; gap: 8px; }
  .contact .icon { width: 12px; height: 12px; flex: none; }
  .contact .spacer { height: 3px; }
</style>
</head>
<body>

<section class="card card--services" aria-label="Services side of business card">
  <div class="world-map-area" role="img" aria-label="Faint world map in the background"></div>
  <div class="services">
    <p><span class="bullet">»</span>ESL / ENL Language Classes</p>
    <p><span class="bullet">»</span>Private Lessons <span class="sep"><span class="bullet">»</span>Online Tutors</span></p>
    <p><span class="bullet">»</span>PLEXA Training and Testing</p>
    <p><span class="bullet">»</span>Translating &amp; Interpreting Services</p>
    <div class="services__rule"></div>
    <p class="services__contact">Contact us about Over-the-Phone<br>Interpreting in over 200 languages<br>24/7/365</p>
  </div>
  <p class="web">www.<span class="accent">corvanatongue</span>.example</p>
</section>

<section class="card card--contact" aria-label="Contact side of business card">
  <svg class="card__waves" viewBox="0 0 540 309" preserveAspectRatio="none" aria-hidden="true">
    <path d="M0,206 C110,184 220,234 360,194 C440,170 500,128 540,102 L540,309 L0,309 Z" fill="var(--brand-blue)"/>
    <path d="M20,192 C130,168 230,212 362,176 C440,154 500,116 540,88 L540,96 C500,124 440,162 362,184 C230,220 130,178 20,194 Z" fill="var(--ink)"/>
    <path d="M100,176 C185,162 262,192 370,162 C440,142 495,108 530,80 C495,112 442,150 372,170 C262,200 185,170 100,178 Z" fill="var(--ink)"/>
  </svg>

  <div class="brand">
    <span class="brand__dot" aria-hidden="true"></span>
    <p class="brand__name">Corvana<br>Tongue Works<br>LLC</p>
  </div>

  <span class="edge-dot" aria-hidden="true"></span>
  <div class="person">
    <p class="person__name">Rhoda Pelling</p>
    <p class="person__title">President</p>
  </div>

  <p class="tagline">Translating « &nbsp;Interpreting «<br>Language Training «</p>

  <ul class="contact">
    <li>482 Garnet Ave., Ste. 219</li>
    <li>Indianapolis, IN 40917 USA</li>
    <li class="spacer"></li>
    <li>
      <svg class="icon" viewBox="0 0 24 24" aria-hidden="true"><path fill="currentColor" d="M6.6 10.8a15.1 15.1 0 0 0 6.6 6.6l2.2-2.2c.3-.3.7-.4 1-.2 1.1.4 2.3.6 3.6.6.6 0 1 .4 1 1V20c0 .6-.4 1-1 1A17 17 0 0 1 3 4c0-.6.4-1 1-1h3.5c.6 0 1 .4 1 1 0 1.3.2 2.5.6 3.6.1.3 0 .7-.2 1z"/></svg>
      (555) 481-3062
    </li>
    <li>
      <svg class="icon" viewBox="0 0 24 24" aria-hidden="true"><path fill="currentColor" d="M2 5h20v14H2z M4 7v.4l8 5 8-5V7l-8 5z" fill-rule="evenodd"/></svg>
      rmpelling@corvanatongueworks.example
    </li>
    <li>
      <svg class="icon" viewBox="0 0 24 24" aria-hidden="true"><circle cx="12" cy="12" r="9.5" fill="none" stroke="currentColor" stroke-width="2"/><path d="M2.5 12h19M12 2.5c3 3 3 16 0 19M12 2.5c-3 3-3 16 0 19" fill="none" stroke="currentColor" stroke-width="1.6"/></svg>
      corvanatongue.example
    </li>
  </ul>
</section>

</body>
</html>
```